Australian Trucking Company Requires Professional Looking Stationary

We require a professional looking stationary design that incorporates our newly designed logo.

Our business, called "Brell Haulage Contracting", provides contracting work, transport and logistics to business in Western Australia particularly with links to the mining sector.

We are a small business looking to expand and our new logo and our new stationary will help develop our brand image in our market place.

Target Market(s)

Businesses and Corporation with links to the Mining Sector

Industry/Entity Type

Small Business

Requirements
Must have
• The letterhead must have the following details:
The new logo

Text saying: "Brell Holdings Pty Ltd (ACN 582 316 907) ATF The Brell Discretionary Trust T/AS"
"ABN 71 834 209 553"
Address "P.O Box 817 Wattlegrove WA, 6958"
Phone: 08 9352 7140
Email: brellhaul@mailbox-example.com.au

The text on the letterhead should be editable as the details are likely to change in the near future. Provision should be made for a website address all though one isn't available at the moment.

The styling, layout and font text is entirely up to the designer.

```html
<!DOCTYPE html>
<html lang="en">
<head>
<meta charset="utf-8">
<title>Brell Haulage Contracting – Business Card</title>
<link href="https://fonts.googleapis.com/css2?family=Open+Sans:wght@400;600;700&display=swap" rel="stylesheet">
<style>
  :root {
    --backdrop: #e9e6e2;
    --card: #ffffff;
    --brand-red: #b3141c;
    --brand-red-dark: #8a0c12;
    --text-dark: #1f1f1f;
    --rule-grey: #7a7a7a;
    --rule-light: #d9d9d9;
  }
  * { box-sizing: border-box; margin: 0; padding: 0; }
  html, body {
    width: 1200px; height: 426px; overflow: hidden;
    background: var(--backdrop);
    font-family: "Open Sans", Arial, sans-serif;
    color: var(--text-dark);
  }
  .canvas { position: relative; width: 1200px; height: 426px; }
  .card {
    position: absolute; background: var(--card);
    border-radius: 18px; overflow: hidden;
    box-shadow: 0 4px 10px rgba(0,0,0,.18);
  }
  .card--front { left: 62px; top: 48px; width: 516px; height: 294px; }
  .card--back  { left: 606px; top: 42px; width: 518px; height: 294px; }

  .brand {
    position: absolute; left: 78px; top: 36px;
    display: flex; align-items: center; gap: 22px;
  }
  .brand__mark { width: 26px; height: 26px; background: var(--brand-red); }
  .brand__name {
    font-size: 29px; font-weight: 700; line-height: 30px;
    color: var(--brand-red); text-transform: uppercase;
  }

  .contact {
    position: absolute; left: 0; width: 100%; text-align: center;
    font-size: 13px; line-height: 20px;
  }
  .contact--primary { top: 153px; }
  .contact--address { top: 173px; }
  .contact__item { display: inline-flex; align-items: center; gap: 3px; margin: 0 4px; }
  .contact__icon { width: 12px; height: 12px; fill: var(--text-dark); }

  .divider {
    position: absolute; left: 66px; right: 66px; top: 202px; height: 1px;
    background: linear-gradient(90deg, transparent, var(--rule-light) 20%, var(--rule-light) 80%, transparent);
  }
  .legal {
    position: absolute; left: 0; width: 100%; top: 214px;
    text-align: center; font-size: 11.5px; line-height: 17px;
  }
  .rule { position: absolute; left: 0; right: 0; height: 2px; background: var(--rule-grey); }
  .rule--top { top: 250px; }
  .rule--bottom { top: 255px; height: 1px; background: var(--rule-light); }
  .name-band {
    position: absolute; left: 0; right: 0; top: 258px; bottom: 0;
    background: linear-gradient(180deg, var(--brand-red) 0%, var(--brand-red-dark) 100%);
    color: #fff; text-align: center; padding-top: 6px;
  }
  .name-band__person { font-size: 18px; font-weight: 700; }
  .name-band__role { font-size: 13px; font-weight: 400; }

  .back-brand {
    position: absolute; inset: 0;
    display: flex; align-items: center; justify-content: center;
    font-size: 30px; font-weight: 700; color: var(--brand-red);
    text-transform: uppercase; text-align: center; line-height: 36px;
  }
</style>
</head>
<body>
<main class="canvas">
  <section class="card card--front">
    <div class="brand">
      <span class="brand__mark"></span>
      <div class="brand__name">Brell Haulage<br>Contracting</div>
    </div>

    <p class="contact contact--primary">
      <span class="contact__item">
        <svg class="contact__icon" viewBox="0 0 24 24"><path d="M6.6 10.8a15 15 0 0 0 6.6 6.6l2.2-2.2a1 1 0 0 1 1-.25 11.4 11.4 0 0 0 3.6.57 1 1 0 0 1 1 1V20a1 1 0 0 1-1 1A17 17 0 0 1 3 4a1 1 0 0 1 1-1h3.5a1 1 0 0 1 1 1c0 1.25.2 2.45.57 3.57a1 1 0 0 1-.25 1z"/></svg>
        08 9352 7140
      </span>
      <span class="contact__item">
        <svg class="contact__icon" viewBox="0 0 24 24"><path d="M2 5h20v14H2zm2 2v.5l8 5 8-5V7zm0 2.8V17h16V9.8l-8 5z"/></svg>
        brellhaul@mailbox-example.com.au
      </span>
    </p>
    <p class="contact contact--address">
      <span class="contact__item">
        <svg class="contact__icon" viewBox="0 0 24 24"><path d="M12 3 2 12h3v8h5v-6h4v6h5v-8h3z"/></svg>
        P.O Box 817 Wattlegrove WA, 6958
      </span>
    </p>

    <div class="divider"></div>

    <p class="legal">
      Brell Holdings Pty Ltd (ACN 582 316 907) ATF The Brell Discretionary Trust T/AS<br>
      ABN 71 834 209 553
    </p>

    <div class="rule rule--top"></div>
    <div class="rule rule--bottom"></div>
    <div class="name-band">
      <span class="name-band__person">Persons name,</span>
      <span class="name-band__role">Manager</span>
    </div>
  </section>

  <section class="card card--back">
    <div class="back-brand">Brell Haulage<br>Contracting</div>
  </section>
</main>
</body>
</html>
```